Business card for medical clinic

I need an upmarket, modern medical/health business card for my clinic

Contact Information for Business Card

name, address, email, qr code

```html
<!DOCTYPE html>
<html lang="en">
<head>
<meta charset="utf-8">
<title>Aurel Health Partners – Business Card</title>
<link rel="stylesheet" href="https://fonts.googleapis.com/css2?family=Cinzel:wght@500&family=Noto+Serif:wght@400&display=swap">
<style>
  :root {
    --page-bg: #d4d5d7;
    --navy: #2a2f45;
    --sky: #38b0de;
    --brand-blue: #1e5f96;
    --accent-blue: #2f8fd0;
    --ink: #2b2b2b;
    --white: #ffffff;
  }
  * { margin: 0; padding: 0; box-sizing: border-box; }
  html, body { width: 900px; height: 1200px; overflow: hidden; }
  body { background: var(--page-bg); position: relative; font-family: "Noto Serif", Georgia, serif; }

  .card { position: absolute; left: 133px; width: 633px; height: 364px; }
  .card-front {
    top: 210px;
    background: linear-gradient(90deg, var(--navy) 0%, #354a66 30%, #3f7da3 60%, var(--sky) 92%);
  }
  .card-back { top: 624px; background: var(--white); }

  .brand { position: absolute; display: flex; align-items: center; gap: 14px; white-space: nowrap; }
  .brand-ring { flex: none; border-radius: 50%; }
  .brand-name { font-family: "Cinzel", "Times New Roman", serif; font-weight: 500; line-height: 1; letter-spacing: 0.02em; white-space: nowrap; }

  .card-front .brand { left: 50%; top: 50%; transform: translate(-50%, -50%); }
  .card-front .brand-ring { width: 40px; height: 40px; border: 3px solid var(--white); }
  .card-front .brand-name { color: var(--white); font-size: 26px; }

  .card-back .brand { left: 36px; top: 175px; transform: translateY(-50%); gap: 10px; }
  .card-back .brand-ring { width: 28px; height: 28px; border: 3px solid var(--brand-blue); }
  .card-back .brand-name { color: var(--brand-blue); font-size: 17px; }

  .divider { position: absolute; left: 317px; top: 94px; width: 2px; height: 178px; background: var(--accent-blue); }

  .contact { position: absolute; left: 331px; top: 89px; color: var(--ink); }
  .person-name { font-family: "Cinzel", "Times New Roman", serif; font-weight: 500; font-size: 22px; color: var(--brand-blue); letter-spacing: 0.01em; line-height: 1.2; white-space: nowrap; }
  .person-role { font-size: 14px; margin-top: 2px; }
  .address { font-size: 14px; line-height: 22px; margin-top: 11px; }
  .lines { list-style: none; margin-top: 11px; font-size: 14px; }
  .lines li { display: flex; align-items: center; gap: 7px; height: 25px; white-space: nowrap; }
  .lines .phone { letter-spacing: 0.18em; }
  .lines svg { width: 11px; height: 11px; flex: none; fill: var(--brand-blue); }
</style>
</head>
<body>
  <section class="card card-front">
    <div class="brand">
      <span class="brand-ring"></span>
      <span class="brand-name">AUREL HEALTH PARTNERS</span>
    </div>
  </section>

  <section class="card card-back">
    <div class="brand">
      <span class="brand-ring"></span>
      <span class="brand-name">AUREL HEALTH PARTNERS</span>
    </div>

    <div class="divider"></div>

    <div class="contact">
      <h1 class="person-name">DANIEL MARLOW</h1>
      <p class="person-role">Principal Consultant</p>
      <p class="address">PO Box 418250<br>Cedar Falls, Iowa 50613</p>
      <ul class="lines">
        <li>
          <svg viewBox="0 0 24 24" aria-hidden="true"><path d="M6.6 10.8a15.1 15.1 0 0 0 6.6 6.6l2.2-2.2c.3-.3.7-.4 1-.2 1.1.4 2.3.6 3.6.6.6 0 1 .4 1 1V20c0 .6-.4 1-1 1A17 17 0 0 1 3 4c0-.6.4-1 1-1h3.5c.6 0 1 .4 1 1 0 1.3.2 2.5.6 3.6.1.3 0 .7-.2 1z"/></svg>
          <span class="phone">+1-555-204-6631</span>
        </li>
        <li>
          <svg viewBox="0 0 24 24" aria-hidden="true"><path d="M2 5h20v14H2z M3.5 6.5 12 13l8.5-6.5" stroke="#fff" stroke-width="1.5"/></svg>
          <span>info@aurelhealthpartners.com</span>
        </li>
        <li>
          <svg viewBox="0 0 24 24" aria-hidden="true"><circle cx="12" cy="12" r="10"/><path d="M2 12h20M12 2c3 3 3 17 0 20M12 2c-3 3-3 17 0 20M4 7h16M4 17h16" stroke="#fff" stroke-width="1.3" fill="none"/></svg>
          <span>www.aurelhealthpartners.com</span>
        </li>
      </ul>
    </div>
  </section>
</body>
</html>
```